Business Cards for a law firm

Business cards for our law firm. Use our silhoette logo and OAK PARTNERS - check our website (www.oakpartners.example)

Contact Information for Business Card

our silhouette logo, OAK PARTNERS, 800-555-0147, Dorian Pemberton, dorian@oakpartners.example

Requirements
Must have
• our silhouette logo, OAK PARTNERS, 800-555-0147, Dorian Pemberton, dorian@oakpartners.example

```html
<!DOCTYPE html>
<html lang="en">
<head>
<meta charset="utf-8">
<title>Oak Partners — Business Cards</title>
<link rel="stylesheet" href="https://fonts.googleapis.com/css2?family=Montserrat:wght@400;500;700&display=swap">
<style>
  :root {
    --navy: #1f2f6b;
    --navy-deep: #1a2860;
    --navy-faint: #2a3a78;
    --ink: #1c1c1c;
    --card-white: #f7f7f7;
    --backdrop: #e4e4e6;
  }
  * { margin: 0; padding: 0; box-sizing: border-box; }
  html, body {
    width: 1200px; height: 900px; overflow: hidden;
    background: var(--backdrop);
    font-family: "Montserrat", sans-serif;
  }
  .sheet {
    width: 1200px; height: 900px;
    display: flex; flex-direction: column;
    align-items: center; justify-content: center; gap: 60px;
  }
  .card {
    width: 630px; height: 360px;
    border-radius: 22px;
    box-shadow: 0 10px 28px rgba(0,0,0,0.18);
    position: relative; overflow: hidden;
  }
  .card-front {
    background: linear-gradient(180deg, #ffffff 0%, var(--card-white) 100%);
    display: flex; align-items: center;
  }
  .brand {
    width: 300px; padding-left: 70px;
    display: flex; align-items: center; gap: 12px;
  }
  .brand-mark { width: 14px; height: 14px; background: var(--navy); }
  .brand-name {
    color: var(--navy); font-weight: 700; font-size: 24px; letter-spacing: 1px;
  }
  .divider { width: 3px; height: 200px; background: var(--navy); }
  .details { padding-left: 40px; color: var(--ink); }
  .person-name {
    color: var(--navy); font-weight: 700; font-size: 24px; letter-spacing: 1px;
  }
  .person-title { font-size: 14px; font-weight: 500; margin-top: 2px; letter-spacing: 1px; }
  .address { font-size: 15px; line-height: 1.3; margin-top: 24px; }
  .contacts { list-style: none; margin-top: 18px; font-size: 15px; line-height: 1.55; }
  .contacts li { display: flex; align-items: center; gap: 12px; }
  .contacts svg { width: 16px; height: 16px; fill: var(--navy); flex: none; }
  .card-back {
    background: var(--navy);
    display: flex; align-items: center; justify-content: center;
  }
  .back-name {
    color: var(--navy-faint); font-weight: 700; font-size: 48px; letter-spacing: 3px;
    text-shadow: none;
  }
</style>
</head>
<body>
<main class="sheet">
  <section class="card card-front" aria-label="Card front">
    <div class="brand">
      <span class="brand-mark"></span>
      <span class="brand-name">OAK PARTNERS</span>
    </div>
    <div class="divider"></div>
    <div class="details">
      <h1 class="person-name">DORIAN PEMBERTON</h1>
      <p class="person-title">OWNER</p>
      <p class="address">1420 Harbor View Ave #310,<br>Westfield, CA 90000</p>
      <ul class="contacts">
        <li>
          <svg viewBox="0 0 24 24" aria-hidden="true"><path d="M6.6 10.8a15 15 0 0 0 6.6 6.6l2.2-2.2a1 1 0 0 1 1-.25 11.4 11.4 0 0 0 3.6.57 1 1 0 0 1 1 1V20a1 1 0 0 1-1 1A17 17 0 0 1 3 4a1 1 0 0 1 1-1h3.5a1 1 0 0 1 1 1c0 1.25.2 2.45.57 3.57a1 1 0 0 1-.25 1z"/></svg>
          800-555-0147
        </li>
        <li>
          <svg viewBox="0 0 24 24" aria-hidden="true"><path d="M3 5h18v14H3zm2 2v.5l7 4.5 7-4.5V7zm0 2.9V17h14V9.9l-7 4.5z"/></svg>
          dorian@oakpartners.example
        </li>
        <li>
          <svg viewBox="0 0 24 24" aria-hidden="true"><path d="M12 2a10 10 0 1 0 0 20 10 10 0 0 0 0-20zm-1 17.9A8 8 0 0 1 4.1 11H7c.1 3.3 1.6 6.4 4 8.9zM7 9H4.3A8 8 0 0 1 11 4.1C8.7 6 7.2 7.7 7 9zm6 10.9c2.4-2.5 3.9-5.6 4-8.9h2.9a8 8 0 0 1-6.9 8.9zM17 9c-.2-1.3-1.7-3-4-4.9A8 8 0 0 1 19.7 9z"/></svg>
          www.oakpartners.example
        </li>
      </ul>
    </div>
  </section>

  <section class="card card-back" aria-label="Card back">
    <span class="back-name">OAK PARTNERS</span>
  </section>
</main>
</body>
</html>
```